Working Capital graphics

Our business advisory firm requires 9 images to be re-created and improved in the branding of our business.

The 9 images have been uploaded below and the colours and branding of the business can be found at the website www.tallowmereadvisory.com.au

```html
<!DOCTYPE html>
<html lang="en">
<head>
<meta charset="utf-8">
<title>Working Capital Cycle – Next $100 of Sales Volume</title>
<link rel="stylesheet" href="https://fonts.googleapis.com/css2?family=Open+Sans:wght@700&family=Roboto:wght@500&display=swap">
<style>
  :root {
    --bg: #ffffff;
    --ink: #0b2148;
    --label: #ffffff;
    --seg-revenue: #1f869b;
    --seg-cost: #0a2350;
    --seg-operating: #0f3684;
    --seg-tax: #164fba;
    --seg-working-capital: #22a7e2;
    --seg-debt: #2178d2;
    --seg-shortfall: #1b89df;
    --hub: #0dafef;
    --flag: #f39325;
    --pole: #1cb5ee;
  }
  html, body {
    margin: 0;
    padding: 0;
    background: var(--bg);
    overflow: hidden;
  }
  .canvas {
    width: 1200px;
    height: 1000px;
    overflow: hidden;
    position: relative;
  }
  .cycle-diagram {
    display: block;
    width: 1200px;
    height: 1000px;
  }
  .seg-revenue { fill: var(--seg-revenue); }
  .seg-cost { fill: var(--seg-cost); }
  .seg-operating { fill: var(--seg-operating); }
  .seg-tax { fill: var(--seg-tax); }
  .seg-working-capital { fill: var(--seg-working-capital); }
  .seg-debt { fill: var(--seg-debt); }
  .seg-shortfall { fill: var(--seg-shortfall); }
  .ring-gap { fill: var(--bg); }
  .hub { fill: var(--hub); }
  .segment-label {
    font-family: "Roboto", Arial, sans-serif;
    font-weight: 500;
    font-size: 28px;
    fill: var(--label);
    text-anchor: middle;
  }
  .milestone-label {
    font-family: "Roboto", Arial, sans-serif;
    font-weight: 500;
    font-size: 34px;
    fill: var(--ink);
    text-anchor: middle;
  }
  .hub-title {
    font-family: "Open Sans", Arial, sans-serif;
    font-weight: 700;
    font-size: 57px;
    fill: var(--label);
    text-anchor: middle;
  }
  .flag-pole { stroke: var(--pole); stroke-width: 7; stroke-linecap: butt; fill: none; }
  .flag-cloth { fill: var(--flag); }
</style>
</head>
<body>
<div class="canvas">
  <svg class="cycle-diagram" viewBox="0 0 1800 1500" xmlns="http://www.w3.org/2000/svg" role="img" aria-label="Working capital cycle for the next $100 of sales volume">
    <defs>
      <clipPath id="ring-clip">
        <circle cx="858" cy="750" r="587"/>
      </clipPath>
      <symbol id="milestone-flag" viewBox="0 0 70 90" width="70" height="90">
        <line class="flag-pole" x1="4" y1="6" x2="26" y2="86"/>
        <path class="flag-cloth" d="M8 12 C20 4 32 14 44 8 C52 4 58 4 62 6 L60 34 C52 32 44 38 34 40 C24 42 18 36 14 40 Z"/>
      </symbol>
    </defs>

    <g class="ring" clip-path="url(#ring-clip)">
      <polygon class="seg-revenue" points="858,750 617,485 625,323 466,315 250,100 858,-200 858,163 970,277 858,392"/>
      <polygon class="seg-cost" points="858,750 858,392 970,277 858,163 858,-200 1800,-200 1555,215 1323,393 1303,550 1145,535"/>
      <polygon class="seg-operating" points="858,750 1145,535 1303,550 1323,393 1555,215 1900,600 1700,940 1430,880 1298,962 1210,825"/>
      <polygon class="seg-tax" points="858,750 1210,825 1298,962 1430,880 1700,940 1700,1600 1250,1600 1110,1280 965,1228 1017,1073"/>
      <polygon class="seg-working-capital" points="858,750 1017,1073 965,1228 1110,1280 1250,1600 350,1500 510,1222 487,1070 648,1045"/>
      <polygon class="seg-debt" points="858,750 648,1045 487,1070 510,1222 350,1500 0,1300 0,700 277,668 403,574 500,700"/>
      <polygon class="seg-shortfall" points="858,750 500,700 403,574 277,668 0,700 0,200 250,100 466,315 625,323 617,485"/>
    </g>

    <circle class="ring-gap" cx="858" cy="750" r="358"/>
    <circle class="hub" cx="858" cy="750" r="320"/>

    <text class="hub-title" x="858" y="737">NEXT $100 OF</text>
    <text class="hub-title" x="866" y="820">SALES VOLUME</text>

    <g class="segment-labels">
      <text class="segment-label" x="764" y="304">$0</text>
      <text class="segment-label" x="1109" y="383">Cost of Sales</text>
      <text class="segment-label" x="1313" y="624">Operating</text>
      <text class="segment-label" x="1313" y="660">Expenses</text>
      <text class="segment-label" x="1323" y="795">Fixed</text>
      <text class="segment-label" x="1323" y="831">Costs</text>
      <text class="segment-label" x="1245" y="1020">Tax</text>
      <text class="segment-label" x="1177" y="1100">Interest</text>
      <text class="segment-label" x="1090" y="1188">Dividends</text>
      <text class="segment-label" x="875" y="1237">Inv</text>
      <text class="segment-label" x="875" y="1273">Days</text>
      <text class="segment-label" x="729" y="1206">AP</text>
      <text class="segment-label" x="729" y="1242">Days</text>
      <text class="segment-label" x="595" y="1144">AR</text>
      <text class="segment-label" x="595" y="1180">Days</text>
      <text class="segment-label" x="403" y="864">Additional</text>
      <text class="segment-label" x="403" y="900">Debt</text>
      <text class="segment-label" x="465" y="458">Cash</text>
      <text class="segment-label" x="465" y="494">Shortfall</text>
    </g>

    <g class="milestones">
      <text class="milestone-label" x="866" y="95">Revenue $0</text>

      <use href="#milestone-flag" x="1505" y="280"/>
      <text class="milestone-label" x="1430" y="305">Gross</text>
      <text class="milestone-label" x="1430" y="348">Margin</text>
      <text class="milestone-label" x="1430" y="391">$0</text>

      <use href="#milestone-flag" x="1597" y="835"/>
      <text class="milestone-label" x="1538" y="883">EBIT</text>
      <text class="milestone-label" x="1538" y="926">$0</text>

      <use href="#milestone-flag" x="740" y="1360"/>
      <text class="milestone-label" x="912" y="1406">Retained</text>
      <text class="milestone-label" x="912" y="1449">Income $0</text>

      <use href="#milestone-flag" x="40" y="1022"/>
      <text class="milestone-label" x="200" y="1023">After</text>
      <text class="milestone-label" x="200" y="1066">Working</text>
      <text class="milestone-label" x="200" y="1109">Capital</text>
      <text class="milestone-label" x="200" y="1152">$0</text>

      <use href="#milestone-flag" x="62" y="350"/>
      <text class="milestone-label" x="222" y="351">After</text>
      <text class="milestone-label" x="222" y="394">Additional</text>
      <text class="milestone-label" x="222" y="437">Funding</text>
      <text class="milestone-label" x="222" y="480">$0</text>
    </g>
  </svg>
</div>
</body>
</html>
```